Animal Eye Clinic needs a Business card

We are a new veterinary ophthalmology practice (Ridgeline Pet Vision Care) and we need a business card designed. We only see animal eyes - we are not a regular veterinary clinic. We already have a logo. We are looking for a professional, good looking business card to hand out to our clients. We are looking for something simple but professional and contemporary. Our logo is likely the only picture/graphic that needs to be on the card.
Updates

Contact Information for Business Card

Delia Vossman, BSc, DVM, MSc, DipACVO
Veterinary Ophthalmologist

Phone: 250.418.3927
Email: ridgelinepetvisioncare@mailbox-example.net
Website: ridgelinepetvisioncare-example.net
Address: 1874 Thornbury Rd
Kelowna, BC, V1X 4M9

Colors

Designer to choose colors to be used in the design.

Requirements
Must have
• Our logo (attached)

```html
<!DOCTYPE html>
<html lang="en">
<head>
<meta charset="utf-8">
<title>Ridgeline Pet Vision Care – Business Card</title>
<link href="https://fonts.googleapis.com/css2?family=Open+Sans:wght@400;600;700&display=swap" rel="stylesheet">
<style>
  :root {
    --teal: #0a9aad;
    --teal-dark: #08889a;
    --paper: #fbf7f7;
    --ink: #3a3a3a;
    --muted: #8a8a8a;
    --band-grey: #767676;
    --stage: #e6e8ea;
  }
  * { margin: 0; padding: 0; box-sizing: border-box; }
  html, body {
    width: 1200px; height: 782px; overflow: hidden;
    background: var(--stage);
    font-family: "Open Sans", Arial, sans-serif;
  }
  .canvas {
    width: 1200px; height: 782px;
    display: flex; align-items: center; justify-content: center; gap: 40px;
  }
  .card {
    position: relative;
    width: 540px; height: 309px;
    box-shadow: 0 6px 18px rgba(0,0,0,0.18);
    overflow: hidden;
  }

  /* Front */
  .card-front {
    background: var(--teal);
    display: flex; align-items: center; justify-content: center;
  }
  .brand {
    display: flex; align-items: center; gap: 12px;
  }
  .brand-dot {
    width: 34px; height: 34px; border-radius: 50%;
    background: currentColor; flex: none;
  }
  .brand-name {
    font-weight: 700; text-transform: uppercase; line-height: 1.1;
    letter-spacing: 0.02em;
  }
  .card-front .brand { color: #fff; }
  .card-front .brand-name { font-size: 24px; }

  /* Back */
  .card-back { background: var(--paper); }
  .card-back .brand {
    position: absolute; left: 24px; top: 58px; color: var(--teal); gap: 8px;
  }
  .card-back .brand-dot { width: 22px; height: 22px; }
  .card-back .brand-name { font-size: 13.5px; }
  .divider {
    position: absolute; left: 238px; top: 48px; width: 1px; height: 150px;
    background: #cfcfcf;
  }
  .contact {
    position: absolute; left: 252px; top: 46px;
    font-size: 10.5px; color: var(--ink); line-height: 1.45;
  }
  .contact-name {
    color: var(--teal); font-weight: 700; font-size: 14px; letter-spacing: 0.02em;
    line-height: 1.2;
  }
  .contact-credentials { color: var(--muted); letter-spacing: 0.03em; }
  .contact-address { margin-top: 2px; }
  .contact-list { list-style: none; margin-top: 6px; }
  .contact-list li { display: flex; align-items: center; gap: 5px; }
  .contact-list svg { width: 9px; height: 9px; flex: none; fill: var(--teal); }
  .card-bands { position: absolute; left: 0; bottom: 0; width: 540px; height: 60px; }
</style>
</head>
<body>
<main class="canvas">

  <section class="card card-front" aria-label="Card front">
    <div class="brand">
      <span class="brand-dot"></span>
      <span class="brand-name">Ridgeline<br>Pet Vision Care</span>
    </div>
  </section>

  <section class="card card-back" aria-label="Card back">
    <div class="brand">
      <span class="brand-dot"></span>
      <span class="brand-name">Ridgeline<br>Pet Vision Care</span>
    </div>

    <div class="divider"></div>

    <div class="contact">
      <p class="contact-name">DELIA VOSSMAN</p>
      <p class="contact-credentials">BSC, DVM, MSC, DIPACVO</p>
      <p class="contact-title">Veterinary Ophthalmologist</p>
      <p class="contact-address">1874 Thornbury Rd<br>Kelowna, BC, V1X 4M9</p>
      <ul class="contact-list">
        <li>
          <svg viewBox="0 0 24 24" aria-hidden="true"><path d="M6.6 10.8a15.1 15.1 0 0 0 6.6 6.6l2.2-2.2a1 1 0 0 1 1-.25 11.4 11.4 0 0 0 3.6.57 1 1 0 0 1 1 1V20a1 1 0 0 1-1 1A17 17 0 0 1 3 4a1 1 0 0 1 1-1h3.5a1 1 0 0 1 1 1c0 1.25.2 2.45.57 3.57a1 1 0 0 1-.25 1z"/></svg>
          250.418.3927
        </li>
        <li>
          <svg viewBox="0 0 24 24" aria-hidden="true"><path d="M2 5h20v14H2z M2 5l10 8 10-8" /></svg>
          ridgelinepetvisioncare@mailbox-example.net
        </li>
        <li>
          <svg viewBox="0 0 24 24" aria-hidden="true"><circle cx="12" cy="12" r="10"/></svg>
          ridgelinepetvisioncare-example.net
        </li>
      </ul>
    </div>

    <svg class="card-bands" viewBox="0 0 540 60" aria-hidden="true">
      <polygon points="0,34 232,34 222,46 0,46" fill="var(--band-grey)"/>
      <polygon points="244,34 540,34 540,60 226,60" fill="var(--teal)"/>
    </svg>
  </section>

</main>
</body>
</html>
```